Stonebridge Building and Projects business cards

A business card with watermark background (construction work)

Company logo attached

Home improvement projects
House renovations
Bathroom and kitchen renovations
House extensions
New builds and granny flats

Director Omar Haddani
(Phone number)
omar@sbpbuilding.com.au
(Instagram logo) sbp_building

```html
<!DOCTYPE html>
<html lang="en">
<head>
<meta charset="utf-8">
<title>Stonebridge Building and Projects – Business Cards</title>
<link rel="stylesheet" href="https://fonts.googleapis.com/css2?family=Open+Sans:wght@400&family=Questrial&display=swap">
<style>
  :root {
    --stage: #2e2e2e;
    --brand-blue: #2f74bf;
    --card-blue: #4d88cc;
    --card-blue-deep: #3f78bd;
    --card-white: #f6f6f6;
    --photo-light: #e9e9e9;
    --photo-mid: #dcdcdc;
    --ink: #3a3a3a;
    --rule: #4a4a4a;
    --white: #ffffff;
  }
  * { box-sizing: border-box; margin: 0; padding: 0; }
  html, body {
    width: 1200px; height: 624px; overflow: hidden;
    background: var(--stage);
  }
  .sheet { position: relative; width: 1200px; height: 624px; }

  .card {
    position: absolute; top: 156px;
    width: 520px; height: 312px; overflow: hidden;
  }
  .card--back { left: 60px; background: var(--card-blue); }
  .card--front { left: 620px; background: var(--card-white); }

  .card__photo { position: absolute; inset: 0; }
  .card--back .card__photo {
    background: linear-gradient(180deg, var(--card-blue) 0%, var(--card-blue-deep) 100%);
  }
  .card--front .card__photo {
    background: linear-gradient(100deg, var(--card-white) 0%, var(--photo-light) 55%, var(--photo-mid) 100%);
  }

  /* Services list */
  .services {
    position: absolute; inset: 0;
    font-family: "Open Sans", sans-serif; font-size: 11.5px;
    color: var(--white); list-style: none;
  }
  .services__item { position: absolute; white-space: nowrap; }
  .services__item svg { position: absolute; left: -22px; top: 2px; width: 10px; height: 10px; }
  .services__item--a { left: 80px;  top: 122px; }
  .services__item--b { left: 284px; top: 122px; }
  .services__item--c { left: 80px;  top: 146px; }
  .services__item--d { left: 284px; top: 146px; }
  .services__item--e { left: 200px; top: 174px; }

  /* Identity block */
  .identity {
    position: absolute; left: 20px; top: 104px; width: 200px;
    text-align: center; font-family: "Questrial", sans-serif;
  }
  .identity__mark {
    display: block; width: 22px; height: 22px; margin: 0 auto 8px;
    background: var(--brand-blue);
  }
  .identity__name { font-size: 18px; color: var(--brand-blue); line-height: 1.1; }
  .identity__sub {
    font-size: 9px; letter-spacing: 3px; color: var(--ink);
    text-transform: uppercase; margin-top: 4px;
  }
  .identity__tagline {
    display: inline-block; margin-top: 6px; font-size: 11px;
    color: var(--brand-blue); border-bottom: 1px solid var(--brand-blue); padding-bottom: 1px;
  }

  .divider {
    position: absolute; left: 225px; top: 89px;
    width: 1px; height: 134px; background: var(--rule);
  }

  .contact {
    position: absolute; left: 239px; top: 98px;
    font-family: "Questrial", sans-serif; color: var(--ink);
  }
  .contact__name { font-size: 24px; color: var(--brand-blue); line-height: 1.1; }
  .contact__role { font-size: 13.5px; margin-top: 2px; }
  .contact__list { list-style: none; margin-top: 12px; font-size: 13.5px; }
  .contact__item { display: flex; align-items: center; gap: 7px; height: 21px; }
  .contact__icon { width: 12px; height: 12px; flex: none; }
</style>
</head>
<body>
<main class="sheet">

  <section class="card card--back" aria-label="Business card back">
    <div class="card__photo" role="img" aria-label="Blue-toned photo of a construction site with a crane and workers"></div>
    <ul class="services">
      <li class="services__item services__item--a"><svg viewBox="0 0 10 10"><path d="M1 5.5 L4 8.5 L9 1.5" fill="none" stroke="#fff" stroke-width="1.2"/></svg>Home improvement projects</li>
      <li class="services__item services__item--b"><svg viewBox="0 0 10 10"><path d="M1 5.5 L4 8.5 L9 1.5" fill="none" stroke="#fff" stroke-width="1.2"/></svg>Bathroom and kitchen renovations</li>
      <li class="services__item services__item--c"><svg viewBox="0 0 10 10"><path d="M1 5.5 L4 8.5 L9 1.5" fill="none" stroke="#fff" stroke-width="1.2"/></svg>House renovations</li>
      <li class="services__item services__item--d"><svg viewBox="0 0 10 10"><path d="M1 5.5 L4 8.5 L9 1.5" fill="none" stroke="#fff" stroke-width="1.2"/></svg>House extensions</li>
      <li class="services__item services__item--e"><svg viewBox="0 0 10 10"><path d="M1 5.5 L4 8.5 L9 1.5" fill="none" stroke="#fff" stroke-width="1.2"/></svg>New builds and granny flats</li>
    </ul>
  </section>

  <section class="card card--front" aria-label="Business card front">
    <div class="card__photo" role="img" aria-label="Faded light grey photo of a construction worker on site"></div>

    <div class="identity">
      <span class="identity__mark"></span>
      <div class="identity__name">Stonebridge</div>
      <div class="identity__sub">Building and Projects</div>
      <div class="identity__tagline">Built right, first time</div>
    </div>

    <div class="divider"></div>

    <div class="contact">
      <h1 class="contact__name">Omar Haddani</h1>
      <p class="contact__role">Director</p>
      <ul class="contact__list">
        <li class="contact__item">
          <svg class="contact__icon" viewBox="0 0 12 12"><circle cx="6" cy="6" r="6" fill="var(--brand-blue)"/><path d="M4 3 L5 3 L5.6 4.6 L4.9 5.2 Q5.6 6.6 6.9 7.2 L7.5 6.5 L9 7.1 L9 8.1 Q8.5 9 7.4 8.8 Q4.2 7.9 3.3 4.4 Q3.3 3.3 4 3 Z" fill="#fff"/></svg>
          0412 580 736
        </li>
        <li class="contact__item">
          <svg class="contact__icon" viewBox="0 0 12 12"><circle cx="6" cy="6" r="6" fill="var(--brand-blue)"/><rect x="3" y="4" width="6" height="4.2" fill="#fff"/><path d="M3 4 L6 6.3 L9 4" fill="none" stroke="var(--brand-blue)" stroke-width="0.7"/></svg>
          omar@sbpbuilding.com.au
        </li>
        <li class="contact__item">
          <svg class="contact__icon" viewBox="0 0 12 12"><circle cx="6" cy="6" r="6" fill="var(--brand-blue)"/></svg>
          sbp_building
        </li>
      </ul>
    </div>
  </section>

</main>
</body>
</html>
```